Harbourline Electrical Solutions

On one side. LOGO (underneath:) Commercial Industrial Residential

- NAME & CONTACT DETAILS

Marcus T. Hollings
Project Manager

(Cell icon) (441) 555-0187
(Email icon) hlelectricalsolutions@mailvento.com
(Facebook & Instagram icons )@hlelectricalsolutions

Other side: LOGO - underneath ELECTRICAL CONSTRUCTION & MAINTENANCE . LED LIGHTING & AUTOMATION . LIFE SAFETY SYSTEMS (FIRE ALARM / SECURITY) . DATA & COMMUNICATION

```html
<!DOCTYPE html>
<html lang="en">
<head>
<meta charset="utf-8">
<title>Harbourline Electrical Solutions – Business Card</title>
<link href="https://fonts.googleapis.com/css2?family=Poppins:wght@400;500;600&display=swap" rel="stylesheet">
<style>
  :root {
    --teal: #0f5068;
    --teal-dark: #0b3f53;
    --ink: #3a3a3a;
    --paper: #ffffff;
    --backdrop: #e6e9ea;
  }
  * { box-sizing: border-box; margin: 0; padding: 0; }
  html, body { width: 1200px; height: 900px; overflow: hidden; }
  body {
    background: var(--backdrop);
    font-family: "Poppins", sans-serif;
    display: flex; flex-direction: column; align-items: center; justify-content: center;
    gap: 40px;
  }
  .card {
    width: 700px; height: 400px; position: relative; overflow: hidden;
    box-shadow: 0 6px 18px rgba(0,0,0,.12);
  }

  /* Back side */
  .card--back {
    background: linear-gradient(135deg, var(--teal) 0%, var(--teal-dark) 100%);
    color: var(--paper);
    display: flex; flex-direction: column; justify-content: center; padding: 0 70px;
  }
  .brand {
    display: flex; align-items: center; gap: 16px;
    font-weight: 600; text-transform: uppercase; letter-spacing: 3px; line-height: 1.15;
  }
  .brand__mark { width: 22px; height: 22px; background: currentColor; flex: none; }
  .card--back .brand { font-size: 30px; }
  .services {
    margin-top: 34px; font-size: 14px; font-weight: 400; line-height: 1.7; letter-spacing: .3px;
  }

  /* Front side */
  .card--front { background: var(--paper); }
  .side-band {
    position: absolute; top: 0; right: 0; width: 74px; height: 100%;
    background: var(--teal);
    display: flex; align-items: center; justify-content: center;
  }
  .side-band__text {
    writing-mode: vertical-rl; color: var(--paper);
    font-size: 14px; letter-spacing: .5px; white-space: nowrap;
  }
  .edge-bar {
    position: absolute; left: 0; bottom: 40px; width: 14px; height: 90px; background: var(--teal);
  }
  .front-content { position: absolute; left: 70px; top: 56px; right: 110px; }
  .card--front .brand { color: var(--teal); font-size: 26px; }
  .person { margin-top: 46px; }
  .person__name {
    color: var(--teal); font-weight: 600; font-size: 22px; text-transform: uppercase; letter-spacing: .5px;
  }
  .person__title { color: var(--ink); font-size: 16px; margin-top: 2px; }
  .contacts { margin-top: 26px; list-style: none; }
  .contacts li {
    display: flex; align-items: center; gap: 10px;
    color: var(--ink); font-size: 15px; margin-bottom: 8px;
  }
  .icon { width: 22px; height: 22px; flex: none; }
  .icon-pair { display: flex; gap: 4px; }
</style>
</head>
<body>

  <section class="card card--back" aria-label="Card back">
    <div class="brand"><span class="brand__mark"></span><span>Harbourline<br>Electrical<br>Solutions</span></div>
    <p class="services">
      Electrical Construction &amp; Maintenance | LED Lighting &amp; Automation<br>
      Life Safety Systems (FIRE ALARM / SECURITY) | Data &amp; Communication
    </p>
  </section>

  <section class="card card--front" aria-label="Card front">
    <div class="front-content">
      <div class="brand"><span class="brand__mark"></span><span>Harbourline Electrical Solutions</span></div>
      <div class="person">
        <p class="person__name">Marcus T. Hollings</p>
        <p class="person__title">Project Manager</p>
      </div>
      <ul class="contacts">
        <li>
          <svg class="icon" viewBox="0 0 22 22" aria-hidden="true">
            <circle cx="11" cy="11" r="11" fill="#0f5068"/>
            <rect x="7.5" y="5" width="7" height="12" rx="1.5" fill="none" stroke="#fff" stroke-width="1.4"/>
            <circle cx="11" cy="14.8" r=".9" fill="#fff"/>
          </svg>
          (441) 555-0187
        </li>
        <li>
          <svg class="icon" viewBox="0 0 22 22" aria-hidden="true">
            <circle cx="11" cy="11" r="11" fill="#0f5068"/>
            <rect x="5.5" y="7" width="11" height="8" rx="1" fill="none" stroke="#fff" stroke-width="1.4"/>
            <path d="M5.8 7.4 11 11.6 16.2 7.4" fill="none" stroke="#fff" stroke-width="1.4"/>
          </svg>
          hlelectricalsolutions@mailvento.com
        </li>
        <li>
          <span class="icon-pair" aria-hidden="true">
            <svg class="icon" viewBox="0 0 22 22"><circle cx="11" cy="11" r="11" fill="#0f5068"/></svg>
            <svg class="icon" viewBox="0 0 22 22"><circle cx="11" cy="11" r="11" fill="#0f5068"/></svg>
          </span>
          @hlelectricalsolutions
        </li>
      </ul>
    </div>
    <div class="edge-bar"></div>
    <div class="side-band"><span class="side-band__text">Commercial | Industrial | Residential</span></div>
  </section>

</body>
</html>
```